Washing powder bag design.

Project Description – Graphic Design Proposal for ORNE Laundry Powder Packaging
We have already explored initial design ideas internally, supported by AI-assisted tools (ChatGPT) to develop early concepts, layouts, and mockups. To support this, we have attached the bag die-cut, where graphics and text are placed as a visual guideline for the intended structure. In addition, we have included a mockup of the product series currently under development to clearly communicate the desired style, direction, and overall visual identity.
The mockup should be regarded as the design foundation for this project and as a starting point for professional refinement.
Scope of Work
We would like you to create three graphic design variants, each based on a different color direction:
1. Variant 1: In line with our current color scheme
2. Variant 2: A blue version
3. Variant 3: A green version
Design Elements to Be Preserved
The following elements must be maintained across all three variants:
• The overall style and visual expression of the mockup
• The leaf-shaped element in the bottom right corner
• The ORNE layout, including typography, positioning, and general look & feel
Summary
While the color palette may vary, the structure, style, and key design elements must remain consistent and be directly based on the attached mockup.
We look forward to seeing your creative interpretation and professional input.
Updates
We need the design to be created based on the attached die-cut file “Orne 10 kg BAG 202526”, including all text elements.
We would like the final to include both the designed die-cut file and a mockup.

```html
<!DOCTYPE html>
<html lang="da">
<head>
<meta charset="utf-8">
<title>ORNE Detergent Packaging Design</title>
<link href="https://fonts.googleapis.com/css2?family=Montserrat:wght@500;600;700;800;900&display=swap" rel="stylesheet">
<style>
  :root{
    --page:#ffffff;
    --title-bg:#0b0b0b;
    --title-ink:#ffffff;
    --panel:#f7f7f4;
    --panel-line:#3a3a3a;
    --text-dark:#1c1c1c;
    --hazard:#d8232a;
  }
  *{box-sizing:border-box;margin:0;padding:0}
  html,body{width:900px;height:1200px;overflow:hidden;background:var(--page)}
  body{position:relative;font-family:"Montserrat",Arial,sans-serif}

  .title-bar{position:absolute;left:285px;top:95px;width:615px;height:68px;background:var(--title-bg);border-radius:34px 0 0 34px;display:flex;align-items:center;padding-left:38px}
  .title-bar h1{color:var(--title-ink);font-size:24px;font-weight:800;letter-spacing:2.4px;white-space:nowrap}

  /* colour directions */
  .v-blue{--bg:#cfe5ef;--bg2:#bcd9e6;--ink:#0f4a64;--stripe:#1b6a86;--mid:#1f93bd;--disc:#bfe0ec;--leaf:#5fb9dc}
  .v-sand{--bg:#e9e2d3;--bg2:#ddd5c2;--ink:#244a35;--stripe:#3d6a4d;--mid:#a9a792;--disc:#c8cdaf;--leaf:#9fae8a}
  .v-green{--bg:#dcebcd;--bg2:#cde0b8;--ink:#2f5a23;--stripe:#4a7a34;--mid:#8db45a;--disc:#9fc36c;--leaf:#9fca73}
  .v-earth{--bg:#ebe2cf;--bg2:#dfd3ba;--ink:#4a3e2b;--stripe:#6b5b40;--mid:#8f7c58;--disc:#cdbd97;--leaf:#b8a67e}

  .bag{position:absolute;width:195px;height:320px;background:linear-gradient(90deg,var(--bg2) 0%,var(--bg) 12%,var(--bg) 88%,var(--bg2) 100%);border-radius:3px 3px 8px 8px;overflow:hidden;box-shadow:0 8px 10px -6px rgba(0,0,0,.35)}

  .hole{position:absolute;top:19px;width:16px;height:16px;border-radius:50%;background:#ffffff;z-index:3}
  .hole:nth-of-type(1){left:65px}.hole:nth-of-type(2){left:90px}.hole:nth-of-type(3){left:115px}

  /* front */
  .band{position:absolute;left:31px;top:0;width:133px;height:110px;background:repeating-linear-gradient(90deg,var(--ink) 0 4px,var(--stripe) 4px 6px)}
  .leaf-deco{position:absolute;border-radius:90% 0 90% 0}
  .leaf-deco--side{right:-14px;top:116px;width:44px;height:56px;background:linear-gradient(135deg,rgba(255,255,255,.7),rgba(255,255,255,.15));transform:rotate(-20deg)}
  .leaf-deco--corner{right:-12px;top:228px;width:74px;height:86px;background:linear-gradient(150deg,var(--leaf),rgba(255,255,255,0) 85%);opacity:.7}
  .brand-disc{position:absolute;left:33px;top:42px;width:129px;height:129px;border-radius:50%;background:var(--disc);border:6px solid var(--ink);z-index:2;overflow:hidden}
  .disc-leaves{position:absolute;left:22px;top:10px;width:73px;height:105px;border-radius:50% 50% 45% 45%;background:radial-gradient(ellipse at 50% 45%,var(--leaf),rgba(255,255,255,0) 70%);opacity:.75}
  .brand-name{position:absolute;left:0;right:0;top:38px;text-align:center;font-size:29px;line-height:34px;font-weight:900;color:var(--ink);letter-spacing:.3px}
  .product{position:absolute;left:0;width:195px;top:178px;text-align:center;font-size:19px;font-weight:800;color:var(--ink);letter-spacing:.2px}
  .product-en{position:absolute;left:0;width:195px;top:200px;text-align:center;font-size:9.5px;font-weight:700;color:var(--mid)}
  .tagline{position:absolute;left:40px;top:217px;width:113px;height:32px;border-radius:16px;background:var(--ink);box-shadow:0 0 0 2px var(--disc);color:#fff;font-size:8.4px;font-weight:700;line-height:11px;text-align:center;padding-top:5px;z-index:2}

  .care-icons{position:absolute;left:18px;top:270px;display:flex;gap:4px;list-style:none;z-index:2}
  .care-icons li{width:28px;height:28px;border-radius:4px;background:var(--ink);padding:3px}
  .care-icons .face{width:100%;height:100%;border-radius:2px;background:var(--bg);border:1px solid var(--ink);display:flex;align-items:center;justify-content:center;color:var(--ink);font-size:8px;font-weight:700}
  .care-icons svg{width:16px;height:16px}
  .weight{position:absolute;left:135px;top:266px;width:42px;height:42px;border-radius:50%;background:var(--ink);border:2px solid var(--disc);display:flex;align-items:center;justify-content:center;color:#fff;font-size:17px;font-weight:800;letter-spacing:-1px;z-index:2}
  .weight span{font-size:8px;color:var(--mid);margin-top:5px;letter-spacing:0}
  .temps{position:absolute;left:18px;top:302px;font-size:6.6px;font-weight:700;color:var(--ink);white-space:nowrap}

  /* back */
  .guide{position:absolute;left:8px;top:62px;width:76px;height:240px;background:var(--panel);border:1px solid var(--panel-line);border-radius:3px;padding:3px;overflow:hidden;color:var(--text-dark)}
  .guide h3{font-size:3.4px;line-height:4.4px;font-weight:700;background:#111;color:#fff;padding:1px 2px;margin:1px 0 3px}
  .guide p{font-size:3.8px;line-height:5.2px;text-align:center;font-weight:500;margin-bottom:3px}
  .guide .gb{margin-top:6px}
  .warning{position:absolute;left:96px;top:60px;width:68px;height:96px;background:var(--panel);border:1px solid var(--panel-line);border-radius:3px;padding:3px;text-align:center;color:var(--text-dark)}
  .warning h3{display:inline-block;font-size:3.8px;font-weight:700;background:#111;color:#fff;padding:1px 3px}
  .warning svg{display:block;margin:5px auto 4px;width:22px;height:22px}
  .warning p{font-size:3.6px;line-height:5px;font-weight:500}
  .dosage-title{position:absolute;left:86px;width:88px;top:180px;text-align:center;font-size:10px;line-height:11px;font-weight:800;color:var(--ink)}
  .dosage{position:absolute;left:93px;top:206px;width:70px;border-collapse:collapse;color:var(--ink);font-size:3.8px;font-weight:600;text-align:center}
  .dosage td,.dosage th{border:.6px solid var(--ink);padding:1.4px 1px;line-height:4.4px}
  .dosage th{font-weight:600}
  .dosage .size{font-size:6px;font-weight:700}
  .dosage .note{font-size:3.8px;border:none}
  .bag--back .care-icons{left:96px;top:280px;gap:3px}
  .bag--back .care-icons li{width:18px;height:18px;padding:2px}
  .bag--back .care-icons .face{font-size:5.5px}
  .bag--back .care-icons svg{width:10px;height:10px}
  .bag--back .temps{left:96px;top:301px;font-size:4.4px}
</style>
</head>
<body>

<header class="title-bar"><h1>ORNE DETERGENT PACKAGING DESIGN</h1></header>

<!-- front row -->
<article class="bag bag--front v-blue" style="left:46px;top:279px">
  <div class="band"></div><span class="hole"></span><span class="hole"></span><span class="hole"></span>
  <div class="leaf-deco leaf-deco--side" role="img" aria-label="Faint outlined leaf illustration"></div>
  <div class="leaf-deco leaf-deco--corner" role="img" aria-label="Large leaf illustration in the bottom right corner"></div>
  <div class="brand-disc"><div class="disc-leaves" role="img" aria-label="Leafy branch illustration"></div><span class="brand-name">ORNE</span></div>
  <h2 class="product">VASKEPULVER</h2><p class="product-en">LAUNDRY DETERGENT</p>
  <p class="tagline">LIV OG BALANCE<br>I HVERDAGEN</p>
  <ul class="care-icons">
    <li><div class="face">120</div></li>
    <li><div class="face"><svg viewBox="0 0 16 16"><rect x="2" y="2" width="12" height="12" rx="2" fill="none" stroke="currentColor" stroke-width="1.4"/><circle cx="8" cy="9" r="3.4" fill="none" stroke="currentColor" stroke-width="1.6"/></svg></div></li>
    <li><div class="face"><svg viewBox="0 0 16 16"><path d="M2 8h12l-2 6H4z" fill="none" stroke="currentColor" stroke-width="1.2"/><path d="M5 8l3-5 2 2" fill="none" stroke="currentColor" stroke-width="1.2"/></svg></div></li>
  </ul>
  <div class="weight">10<span>kg</span></div>
  <p class="temps">20°C | 30°C | 40°C | 60°C | 90°C</p>
</article>

<article class="bag bag--front v-sand" style="left:251px;top:279px">
  <div class="band"></div><span class="hole"></span><span class="hole"></span><span class="hole"></span>
  <div class="leaf-deco leaf-deco--side" role="img" aria-label="Faint outlined leaf illustration"></div>
  <div class="leaf-deco leaf-deco--corner" role="img" aria-label="Large leaf illustration in the bottom right corner"></div>
  <div class="brand-disc"><div class="disc-leaves" role="img" aria-label="Leafy branch illustration"></div><span class="brand-name">ORNE</span></div>
  <h2 class="product">VASKEPULVER</h2><p class="product-en">LAUNDRY DETERGENT</p>
  <p class="tagline">LIV OG BALANCE<br>I HVERDAGEN</p>
  <ul class="care-icons">
    <li><div class="face">120</div></li>
    <li><div class="face"><svg viewBox="0 0 16 16"><rect x="2" y="2" width="12" height="12" rx="2" fill="none" stroke="currentColor" stroke-width="1.4"/><circle cx="8" cy="9" r="3.4" fill="none" stroke="currentColor" stroke-width="1.6"/></svg></div></li>
    <li><div class="face"><svg viewBox="0 0 16 16"><path d="M2 8h12l-2 6H4z" fill="none" stroke="currentColor" stroke-width="1.2"/><path d="M5 8l3-5 2 2" fill="none" stroke="currentColor" stroke-width="1.2"/></svg></div></li>
  </ul>
  <div class="weight">10<span>kg</span></div>
  <p class="temps">20°C | 30°C | 40°C | 60°C | 90°C</p>
</article>

<article class="bag bag--front v-green" style="left:456px;top:279px">
  <div class="band"></div><span class="hole"></span><span class="hole"></span><span class="hole"></span>
  <div class="leaf-deco leaf-deco--side" role="img" aria-label="Faint outlined leaf illustration"></div>
  <div class="leaf-deco leaf-deco--corner" role="img" aria-label="Large leaf illustration in the bottom right corner"></div>
  <div class="brand-disc"><div class="disc-leaves" role="img" aria-label="Leafy branch illustration"></div><span class="brand-name">ORNE</span></div>
  <h2 class="product">VASKEPULVER</h2><p class="product-en">LAUNDRY DETERGENT</p>
  <p class="tagline">LIV OG BALANCE<br>I HVERDAGEN</p>
  <ul class="care-icons">
    <li><div class="face">120</div></li>
    <li><div class="face"><svg viewBox="0 0 16 16"><rect x="2" y="2" width="12" height="12" rx="2" fill="none" stroke="currentColor" stroke-width="1.4"/><circle cx="8" cy="9" r="3.4" fill="none" stroke="currentColor" stroke-width="1.6"/></svg></div></li>
    <li><div class="face"><svg viewBox="0 0 16 16"><path d="M2 8h12l-2 6H4z" fill="none" stroke="currentColor" stroke-width="1.2"/><path d="M5 8l3-5 2 2" fill="none" stroke="currentColor" stroke-width="1.2"/></svg></div></li>
  </ul>
  <div class="weight">10<span>kg</span></div>
  <p class="temps">20°C | 30°C | 40°C | 60°C | 90°C</p>
</article>

<article class="bag bag--front v-earth" style="left:661px;top:279px">
  <div class="band"></div><span class="hole"></span><span class="hole"></span><span class="hole"></span>
  <div class="leaf-deco leaf-deco--side" role="img" aria-label="Faint outlined leaf illustration"></div>
  <div class="leaf-deco leaf-deco--corner" role="img" aria-label="Large leaf illustration in the bottom right corner"></div>
  <div class="brand-disc"><div class="disc-leaves" role="img" aria-label="Leafy branch illustration"></div><span class="brand-name">ORNE</span></div>
  <h2 class="product">VASKEPULVER</h2><p class="product-en">LAUNDRY DETERGENT</p>
  <p class="tagline">LIV OG BALANCE<br>I HVERDAGEN</p>
  <ul class="care-icons">
    <li><div class="face">120</div></li>
    <li><div class="face"><svg viewBox="0 0 16 16"><rect x="2" y="2" width="12" height="12" rx="2" fill="none" stroke="currentColor" stroke-width="1.4"/><circle cx="8" cy="9" r="3.4" fill="none" stroke="currentColor" stroke-width="1.6"/></svg></div></li>
    <li><div class="face"><svg viewBox="0 0 16 16"><path d="M2 8h12l-2 6H4z" fill="none" stroke="currentColor" stroke-width="1.2"/><path d="M5 8l3-5 2 2" fill="none" stroke="currentColor" stroke-width="1.2"/></svg></div></li>
  </ul>
  <div class="weight">10<span>kg</span></div>
  <p class="temps">20°C | 30°C | 40°C | 60°C | 90°C</p>
</article>

<!-- back row -->
<article class="bag bag--back v-blue" style="left:51px;top:632px;width:186px">
  <span class="hole"></span><span class="hole"></span><span class="hole"></span>
  <section class="guide">
    <h3>(DK) BRUGERVEJLEDNING – ORNE VASKEPULVER</h3>
    <p>Til universel brug. Egnet til alle vaskbare tekstiler fra 20°C til 90°C. Sorter tøjet efter farve og følg vaskeanvisningen. Dosér efter vandets hårdhed og tøjets snavsgrad.</p>
    <p>Anbefalinger: Undgå overdosering, det skåner miljø og maskine. Ved hårdt vand kan ekstra dosering være nødvendig.</p>
    <p>Opbevaring: Opbevares tørt og utilgængeligt for børn. Luk posen efter brug.</p>
    <p>Sikkerhed: Forårsager alvorlig øjenirritation. Ved kontakt med øjnene skylles grundigt med vand.</p>
    <h3 class="gb">(GB) USER GUIDE – ORNE LAUNDRY DETERGENT POWDER</h3>
    <p>Universal detergent. Suitable for all washable textiles from 20°C to 90°C. Sort laundry by colour and follow care labels. Dose according to water hardness and soil level.</p>
    <p>Recommendations: Avoid overdosing to protect the environment and your machine. Very hard water may need extra dosage.</p>
    <p>Storage: Store in a dry place out of reach of children. Keep the bag closed.</p>
    <p>Safety: Causes serious eye irritation. If in eyes, rinse cautiously with water.</p>
  </section>
  <section class="warning">
    <h3>Advarsel Warning</h3>
    <svg viewBox="0 0 22 22"><path d="M11 1.5L20.5 11 11 20.5 1.5 11z" fill="#fff" stroke="var(--hazard)" stroke-width="1.8"/><rect x="10" y="6" width="2" height="7" fill="#111"/><rect x="10" y="14.5" width="2" height="2" fill="#111"/></svg>
    <p>Forårsager alvorlig øjenirritation. Causes serious eye irritation. Keep out of reach of children.</p>
  </section>
  <h2 class="dosage-title">DOSERING<br>DOSAGE</h2>
  <table class="dosage">
    <tr><th></th><th>soft</th><th>medium</th><th>hard</th></tr>
    <tr><td class="size">1Kg</td><td>37 ml ≈41g</td><td>37 ml ≈61g</td><td>83 g</td></tr>
    <tr><td class="size">5Kg</td><td>65 Kg</td><td>37 ml ≈83g</td><td>83 g</td></tr>
    <tr><td class="size">10Kg</td><td>112 Kg</td><td>112 ml ≈124g</td><td>144g</td></tr>
    <tr><td class="note" colspan="4">75 ml = 83g</td></tr>
  </table>
  <ul class="care-icons">
    <li><div class="face">120</div></li>
    <li><div class="face"><svg viewBox="0 0 16 16"><rect x="2" y="2" width="12" height="12" rx="2" fill="none" stroke="currentColor" stroke-width="1.4"/><circle cx="8" cy="9" r="3.4" fill="none" stroke="currentColor" stroke-width="1.6"/></svg></div></li>
    <li><div class="face"><svg viewBox="0 0 16 16"><path d="M2 8h12l-2 6H4z" fill="none" stroke="currentColor" stroke-width="1.2"/><path d="M5 8l3-5 2 2" fill="none" stroke="currentColor" stroke-width="1.2"/></svg></div></li>
  </ul>
  <p class="temps">20°C | 30°C | 40°C | 60°C | 90°C</p>
</article>

<article class="bag bag--back v-sand" style="left:256px;top:632px;width:186px">
  <span class="hole"></span><span class="hole"></span><span class="hole"></span>
  <section class="guide">
    <h3>(DK) BRUGERVEJLEDNING – ORNE VASKEPULVER</h3>
    <p>Til universel brug. Egnet til alle vaskbare tekstiler fra 20°C til 90°C. Sorter tøjet efter farve og følg vaskeanvisningen. Dosér efter vandets hårdhed og tøjets snavsgrad.</p>
    <p>Anbefalinger: Undgå overdosering, det skåner miljø og maskine. Ved hårdt vand kan ekstra dosering være nødvendig.</p>
    <p>Opbevaring: Opbevares tørt og utilgængeligt for børn. Luk posen efter brug.</p>
    <p>Sikkerhed: Forårsager alvorlig øjenirritation. Ved kontakt med øjnene skylles grundigt med vand.</p>
    <h3 class="gb">(GB) USER GUIDE – ORNE LAUNDRY DETERGENT POWDER</h3>
    <p>Universal detergent. Suitable for all washable textiles from 20°C to 90°C. Sort laundry by colour and follow care labels. Dose according to water hardness and soil level.</p>
    <p>Recommendations: Avoid overdosing to protect the environment and your machine. Very hard water may need extra dosage.</p>
    <p>Storage: Store in a dry place out of reach of children. Keep the bag closed.</p>
    <p>Safety: Causes serious eye irritation. If in eyes, rinse cautiously with water.</p>
  </section>
  <section class="warning">
    <h3>Advarsel Warning</h3>
    <svg viewBox="0 0 22 22"><path d="M11 1.5L20.5 11 11 20.5 1.5 11z" fill="#fff" stroke="var(--hazard)" stroke-width="1.8"/><rect x="10" y="6" width="2" height="7" fill="#111"/><rect x="10" y="14.5" width="2" height="2" fill="#111"/></svg>
    <p>Forårsager alvorlig øjenirritation. Causes serious eye irritation. Keep out of reach of children.</p>
  </section>
  <h2 class="dosage-title">DOSERING<br>DOSAGE</h2>
  <table class="dosage">
    <tr><th></th><th>soft</th><th>medium</th><th>hard</th></tr>
    <tr><td class="size">1Kg</td><td>37 ml ≈41g</td><td>37 ml ≈61g</td><td>83 g</td></tr>
    <tr><td class="size">5Kg</td><td>65 Kg</td><td>37 ml ≈83g</td><td>83 g</td></tr>
    <tr><td class="size">10Kg</td><td>112 Kg</td><td>112 ml ≈124g</td><td>144g</td></tr>
    <tr><td class="note" colspan="4">75 ml = 83g</td></tr>
  </table>
  <ul class="care-icons">
    <li><div class="face">120</div></li>
    <li><div class="face"><svg viewBox="0 0 16 16"><rect x="2" y="2" width="12" height="12" rx="2" fill="none" stroke="currentColor" stroke-width="1.4"/><circle cx="8" cy="9" r="3.4" fill="none" stroke="currentColor" stroke-width="1.6"/></svg></div></li>
    <li><div class="face"><svg viewBox="0 0 16 16"><path d="M2 8h12l-2 6H4z" fill="none" stroke="currentColor" stroke-width="1.2"/><path d="M5 8l3-5 2 2" fill="none" stroke="currentColor" stroke-width="1.2"/></svg></div></li>
  </ul>
  <p class="temps">20°C | 30°C | 40°C | 60°C | 90°C</p>
</article>

<article class="bag bag--back v-green" style="left:461px;top:632px;width:186px">
  <span class="hole"></span><span class="hole"></span><span class="hole"></span>
  <section class="guide">
    <h3>(DK) BRUGERVEJLEDNING – ORNE VASKEPULVER</h3>
    <p>Til universel brug. Egnet til alle vaskbare tekstiler fra 20°C til 90°C. Sorter tøjet efter farve og følg vaskeanvisningen. Dosér efter vandets hårdhed og tøjets snavsgrad.</p>
    <p>Anbefalinger: Undgå overdosering, det skåner miljø og maskine. Ved hårdt vand kan ekstra dosering være nødvendig.</p>
    <p>Opbevaring: Opbevares tørt og utilgængeligt for børn. Luk posen efter brug.</p>
    <p>Sikkerhed: Forårsager alvorlig øjenirritation. Ved kontakt med øjnene skylles grundigt med vand.</p>
    <h3 class="gb">(GB) USER GUIDE – ORNE LAUNDRY DETERGENT POWDER</h3>
    <p>Universal detergent. Suitable for all washable textiles from 20°C to 90°C. Sort laundry by colour and follow care labels. Dose according to water hardness and soil level.</p>
    <p>Recommendations: Avoid overdosing to protect the environment and your machine. Very hard water may need extra dosage.</p>
    <p>Storage: Store in a dry place out of reach of children. Keep the bag closed.</p>
    <p>Safety: Causes serious eye irritation. If in eyes, rinse cautiously with water.</p>
  </section>
  <section class="warning">
    <h3>Advarsel Warning</h3>
    <svg viewBox="0 0 22 22"><path d="M11 1.5L20.5 11 11 20.5 1.5 11z" fill="#fff" stroke="var(--hazard)" stroke-width="1.8"/><rect x="10" y="6" width="2" height="7" fill="#111"/><rect x="10" y="14.5" width="2" height="2" fill="#111"/></svg>
    <p>Forårsager alvorlig øjenirritation. Causes serious eye irritation. Keep out of reach of children.</p>
  </section>
  <h2 class="dosage-title">DOSERING<br>DOSAGE</h2>
  <table class="dosage">
    <tr><th></th><th>soft</th><th>medium</th><th>hard</th></tr>
    <tr><td class="size">1Kg</td><td>37 ml ≈41g</td><td>37 ml ≈61g</td><td>83 g</td></tr>
    <tr><td class="size">5Kg</td><td>65 Kg</td><td>37 ml ≈83g</td><td>83 g</td></tr>
    <tr><td class="size">10Kg</td><td>112 Kg</td><td>112 ml ≈124g</td><td>144g</td></tr>
    <tr><td class="note" colspan="4">75 ml = 83g</td></tr>
  </table>
  <ul class="care-icons">
    <li><div class="face">120</div></li>
    <li><div class="face"><svg viewBox="0 0 16 16"><rect x="2" y="2" width="12" height="12" rx="2" fill="none" stroke="currentColor" stroke-width="1.4"/><circle cx="8" cy="9" r="3.4" fill="none" stroke="currentColor" stroke-width="1.6"/></svg></div></li>
    <li><div class="face"><svg viewBox="0 0 16 16"><path d="M2 8h12l-2 6H4z" fill="none" stroke="currentColor" stroke-width="1.2"/><path d="M5 8l3-5 2 2" fill="none" stroke="currentColor" stroke-width="1.2"/></svg></div></li>
  </ul>
  <p class="temps">20°C | 30°C | 40°C | 60°C | 90°C</p>
</article>

<article class="bag bag--back v-earth" style="left:666px;top:632px;width:186px">
  <span class="hole"></span><span class="hole"></span><span class="hole"></span>
  <section class="guide">
    <h3>(DK) BRUGERVEJLEDNING – ORNE VASKEPULVER</h3>
    <p>Til universel brug. Egnet til alle vaskbare tekstiler fra 20°C til 90°C. Sorter tøjet efter farve og følg vaskeanvisningen. Dosér efter vandets hårdhed og tøjets snavsgrad.</p>
    <p>Anbefalinger: Undgå overdosering, det skåner miljø og maskine. Ved hårdt vand kan ekstra dosering være nødvendig.</p>
    <p>Opbevaring: Opbevares tørt og utilgængeligt for børn. Luk posen efter brug.</p>
    <p>Sikkerhed: Forårsager alvorlig øjenirritation. Ved kontakt med øjnene skylles grundigt med vand.</p>
    <h3 class="gb">(GB) USER GUIDE – ORNE LAUNDRY DETERGENT POWDER</h3>
    <p>Universal detergent. Suitable for all washable textiles from 20°C to 90°C. Sort laundry by colour and follow care labels. Dose according to water hardness and soil level.</p>
    <p>Recommendations: Avoid overdosing to protect the environment and your machine. Very hard water may need extra dosage.</p>
    <p>Storage: Store in a dry place out of reach of children. Keep the bag closed.</p>
    <p>Safety: Causes serious eye irritation. If in eyes, rinse cautiously with water.</p>
  </section>
  <section class="warning">
    <h3>Advarsel Warning</h3>
    <svg viewBox="0 0 22 22"><path d="M11 1.5L20.5 11 11 20.5 1.5 11z" fill="#fff" stroke="var(--hazard)" stroke-width="1.8"/><rect x="10" y="6" width="2" height="7" fill="#111"/><rect x="10" y="14.5" width="2" height="2" fill="#111"/></svg>
    <p>Forårsager alvorlig øjenirritation. Causes serious eye irritation. Keep out of reach of children.</p>
  </section>
  <h2 class="dosage-title">DOSERING<br>DOSAGE</h2>
  <table class="dosage">
    <tr><th></th><th>soft</th><th>medium</th><th>hard</th></tr>
    <tr><td class="size">1Kg</td><td>37 ml ≈41g</td><td>37 ml ≈61g</td><td>83 g</td></tr>
    <tr><td class="size">5Kg</td><td>65 Kg</td><td>37 ml ≈83g</td><td>83 g</td></tr>
    <tr><td class="size">10Kg</td><td>112 Kg</td><td>112 ml ≈124g</td><td>144g</td></tr>
    <tr><td class="note" colspan="4">75 ml = 83g</td></tr>
  </table>
  <ul class="care-icons">
    <li><div class="face">120</div></li>
    <li><div class="face"><svg viewBox="0 0 16 16"><rect x="2" y="2" width="12" height="12" rx="2" fill="none" stroke="currentColor" stroke-width="1.4"/><circle cx="8" cy="9" r="3.4" fill="none" stroke="currentColor" stroke-width="1.6"/></svg></div></li>
    <li><div class="face"><svg viewBox="0 0 16 16"><path d="M2 8h12l-2 6H4z" fill="none" stroke="currentColor" stroke-width="1.2"/><path d="M5 8l3-5 2 2" fill="none" stroke="currentColor" stroke-width="1.2"/></svg></div></li>
  </ul>
  <p class="temps">20°C | 30°C | 40°C | 60°C | 90°C</p>
</article>

</body>
</html>
```